equestrian poster

Could you make the poster an elete looking poster for a sports event using the building on the back ground and photo shop the horse there also please make an sporty luxery poster
the dates for next year are 27th till 31 st may and 16 till 19 plus 23rd till 26 juli

our colors are green and gray

Target Market(s)

tourist and public

Industry/Entity Type

equestrian event interna

Other font styles liked:
• caslon classico font

Colors
00AB8E
00BBA5
67D7C9
C6EFE9
E9F9F6

```html
<!DOCTYPE html>
<html lang="en">
<head>
<meta charset="utf-8">
<title>CH De Heide – Show Jumping Poster</title>
<link rel="stylesheet" href="https://fonts.googleapis.com/css2?family=Bebas+Neue&family=Poppins:wght@300;500;700;800&display=swap">
<style>
  :root {
    --paper: #f4f4f2;
    --green-deep: #0c3d31;
    --green-dark: #00604f;
    --green: #00ab8e;
    --green-bright: #00bba5;
    --mint: #67d7c9;
    --mint-light: #c6efe9;
    --mint-pale: #e9f9f6;
    --aqua-text: #4ff0d0;
    --ink: #1d1d1d;
    --rule: #b9bdbb;
  }
  * { box-sizing: border-box; margin: 0; padding: 0; }
  html, body { width: 856px; height: 1200px; overflow: hidden; }
  body {
    background: var(--paper);
    font-family: "Poppins", sans-serif;
    color: var(--ink);
    position: relative;
  }
  .poster { position: absolute; inset: 0; }

  .brand {
    position: absolute; top: 42px; left: 0; right: 0;
    display: flex; flex-direction: column; align-items: center;
  }
  .brand-dot {
    width: 90px; height: 90px; border-radius: 50%;
    border: 3px solid var(--green-dark);
  }
  .brand-name {
    margin-top: 16px;
    font-family: "Poppins", sans-serif;
    font-weight: 500;
    font-size: 24px; line-height: 1; color: var(--green-deep); letter-spacing: 0.5px;
  }

  .headline {
    position: absolute; top: 205px; left: 0; right: 0;
    text-align: center;
    font-family: "Bebas Neue", sans-serif;
    font-weight: 400;
    font-size: 200px; line-height: 1; letter-spacing: 2px;
    transform: scaleY(1.17); transform-origin: top center;
    background: linear-gradient(180deg, var(--green-bright) 0%, var(--green) 45%, #0a5a46 100%);
    -webkit-background-clip: text; background-clip: text;
    color: transparent;
  }

  .hero {
    position: absolute; left: 96px; top: 400px; width: 680px; height: 530px;
    border-radius: 42% 58% 40% 60% / 34% 40% 60% 66%;
    transform: rotate(-6deg);
    background:
      radial-gradient(ellipse 30% 50% at 44% 55%, #9a5f34 0%, rgba(154,95,52,0.6) 45%, rgba(154,95,52,0) 75%),
      linear-gradient(180deg, var(--mint) 0%, #86ddd0 55%, var(--mint-pale) 100%);
  }

  .since {
    position: absolute; left: 254px; top: 802px; width: 348px; height: 55px;
    background: var(--green-dark);
    display: flex; align-items: center; justify-content: center; gap: 14px;
    font-weight: 800; font-size: 36px; letter-spacing: 5px;
    color: #fff;
  }
  .since-year { color: var(--aqua-text); }

  .dates {
    position: absolute; top: 918px; left: 60px; right: 60px; height: 170px;
    display: grid; grid-template-columns: 255px 213px 1fr;
  }
  .date-range {
    display: flex; flex-direction: column; align-items: flex-start;
    justify-content: center; gap: 4px;
  }
  .date-range:nth-child(1) { padding-left: 60px; }
  .date-range:nth-child(2) { padding-left: 26px; }
  .date-range:nth-child(3) { padding-left: 28px; }
  .date-range + .date-range { border-left: 1px solid var(--rule); }
  .date {
    display: flex; align-items: flex-end; color: var(--green-deep);
  }
  .date-day { font-weight: 700; font-size: 78px; line-height: 0.78; letter-spacing: -4px; }
  .date-meta { display: flex; flex-direction: column; margin-left: 3px; line-height: 0.82; }
  .date-suffix { font-weight: 700; font-size: 25px; }
  .date-month { font-weight: 700; font-size: 38px; letter-spacing: -0.5px; }
  .date-to {
    width: 17px; height: 17px; border-radius: 50%;
    background: var(--mint); color: var(--green-deep);
    font-size: 8px; font-style: italic; display: flex;
    align-items: center; justify-content: center;
    margin: 4px 0 4px 24px;
  }

  .footer {
    position: absolute; top: 1124px; left: 106px; right: 82px;
    display: flex; align-items: center; justify-content: space-between;
  }
  .social { display: flex; align-items: center; gap: 10px; font-weight: 300; font-size: 18px; letter-spacing: 0.6px; }
  .social-dot { width: 20px; height: 20px; border-radius: 50%; background: var(--green); }
  .website { font-size: 22px; font-weight: 500; }
  .website-name { color: var(--green-dark); font-weight: 700; }
</style>
</head>
<body>
<main class="poster">
  <header class="brand">
    <span class="brand-dot"></span>
    <span class="brand-name">De Heide Equestrian</span>
  </header>

  <h1 class="headline">CH DE HEIDE</h1>

  <div class="hero" role="img" aria-label="Show jumper on a bay horse clearing a fence, in front of the equestrian centre building on a mint brush-stroke backdrop"></div>

  <div class="since"><span>SINCE</span><span class="since-year">2005</span></div>

  <section class="dates">
    <div class="date-range">
      <div class="date"><span class="date-day">16</span><span class="date-meta"><span class="date-suffix">TH</span><span class="date-month">JUNE</span></span></div>
      <span class="date-to">to</span>
      <div class="date"><span class="date-day">19</span><span class="date-meta"><span class="date-suffix">TH</span><span class="date-month">JUNE</span></span></div>
    </div>
    <div class="date-range">
      <div class="date"><span class="date-day">27</span><span class="date-meta"><span class="date-suffix">TH</span><span class="date-month">MAY</span></span></div>
      <span class="date-to">to</span>
      <div class="date"><span class="date-day">31</span><span class="date-meta"><span class="date-suffix">ST</span><span class="date-month">MAY</span></span></div>
    </div>
    <div class="date-range">
      <div class="date"><span class="date-day">23</span><span class="date-meta"><span class="date-suffix">RD</span><span class="date-month">JUNE</span></span></div>
      <span class="date-to">to</span>
      <div class="date"><span class="date-day">26</span><span class="date-meta"><span class="date-suffix">TH</span><span class="date-month">JUNE</span></span></div>
    </div>
  </section>

  <footer class="footer">
    <div class="social"><span class="social-dot"></span><span>CH De Heide - CSI** OUDEVELD</span></div>
    <div class="website">www.<span class="website-name">chdeheide</span>.nl</div>
  </footer>
</main>
</body>
</html>
```